Wellness, Meaning, and the Inner Journey Research Program Website

Overview: This website will serve a new research program (Wellness, Meaning, and the Inner Journey) at the Harrowgate University School of Medicine. I want a clean, intuitive design that has a navigation bar, but uses icons/graphic buttons to link to the main pages. In an attached Word document, I have provided a basic information architecture for the site, understanding that this project would just generate graphics and code for the 3 pages. I highlighted the 3 pages I'd like designed.
Target market: People who want to participate in our research, or contribute grant funding to specific projects.
Number of page: The design project focuses on 3 pages, but the site must accommodate 6 pages with top-level links. See attached Word doc.
Logo and website header: Please integrate our logo in the header. I've uploaded it as a png file--both with the name of the website and with just the logo image. I imaging the logo would look great in a banner set against an image of a mountain. The two main design themes I want to see included are nature and healthcare.
Text content: I have not yet provided text. Use some dummy text.
Technical Specifications:
- Build using WordPress. We will host this site ourselves on NetHarbor using WordPress.
- The design package must be coded.
- The template must be responsive to different platforms (e.g., computer, mobile phone, iPad).
Thank you! I look forward to seeing your designs.
- Ned

```html
<!DOCTYPE html>
<html lang="en">
<head>
<meta charset="utf-8">
<title>Wellness, Meaning, and the Inner Journey – Research Program</title>
<link rel="stylesheet" href="https://fonts.googleapis.com/css2?family=Exo+2:wght@500;600;700;800&family=Poppins:wght@300;400;500;600&display=swap">
<style>
:root{
  --teal:#12b69c;
  --teal-dark:#0a9c80;
  --green:#4f9f3a;
  --blue:#0b4fae;
  --blue-deep:#0a3f95;
  --ink:#1f2a37;
  --muted:#6b7280;
  --line:#e3e7ec;
  --white:#ffffff;
  --pill:#e6eefb;
}
*{margin:0;padding:0;box-sizing:border-box}
html,body{width:1200px;height:4115px;overflow:hidden}
body{position:relative;background:var(--white);font-family:"Poppins",sans-serif;color:var(--ink)}
.abs{position:absolute}
.heading{font-family:"Exo 2",sans-serif;font-weight:600;color:var(--blue)}
.center{text-align:center}
.tagline{color:var(--green);font-size:15px}
.copy{color:var(--muted);font-size:12px;line-height:21px}

/* header */
.hero-shape{left:0;top:0;width:1200px;height:720px}
.brand{left:60px;top:22px;display:flex;align-items:center;gap:12px}
.brand-dot{width:48px;height:48px;border-radius:50%;background:var(--white);border:3px solid var(--teal)}
.brand-name{font-size:11px;font-weight:600;color:var(--blue);line-height:14px}
.brand-name span{display:block;color:var(--green);font-weight:500;font-size:10px}
.nav{top:44px;left:607px;display:flex;gap:0}
.nav a{position:absolute;font-size:12.5px;color:var(--ink);text-decoration:none;white-space:nowrap}
.nav a.active{color:var(--teal)}
.nav a.active::after{content:"";position:absolute;left:50%;top:22px;width:5px;height:5px;margin-left:-2.5px;border-radius:50%;background:var(--teal)}
.call{left:988px;top:-36px;width:154px;height:146px;border-radius:50%;background:linear-gradient(160deg,#1a72d6,var(--blue-deep));box-shadow:0 0 0 4px rgba(11,79,174,.25);color:var(--white);text-align:center;padding-top:42px}
.call svg{display:block;margin:0 auto 2px}
.call small{font-size:11px;display:block}
.call b{font-size:16px;font-weight:500;letter-spacing:.5px}

/* hero */
.hero-title{left:61px;top:172px;font-family:"Exo 2",sans-serif;font-weight:800;font-size:44px;line-height:45px;color:var(--white);text-transform:uppercase}
.hero-title em{font-style:normal;color:var(--blue)}
.hero-lede{left:61px;top:355px;width:400px;font-size:13px;line-height:21px;color:var(--white)}
.hero-icons{left:52px;top:430px;display:flex}
.hero-icon{width:106px;height:86px;text-align:center;color:var(--white);font-size:12px;border-right:1px solid rgba(255,255,255,.35)}
.hero-icon:last-child{border-right:none}
.hero-icon svg{display:block;margin:4px auto 10px}
.dots{left:61px;top:638px;display:flex;gap:6px}
.dots i{width:8px;height:8px;border-radius:50%;background:rgba(255,255,255,.75)}
.dots i.on{background:var(--blue);box-shadow:0 0 0 2px var(--white)}
.hero-photo{left:465px;top:219px;width:675px;height:449px;background:linear-gradient(160deg,#e8efe4 0%,#9fb9a4 45%,#3f6b3e 100%)}

/* vision */
.vision-title{top:758px;left:0;width:1200px;font-size:36px}
.vision-sub{top:812px;left:0;width:1200px;line-height:22px}
.vision-sub span{display:block;font-size:13px}
.vision-copy{top:866px;left:340px;width:520px;font-size:11.5px}
.tiles{top:964px;left:217px;display:flex;gap:20px}
.tile{width:242px;height:211px;border-radius:30px;color:var(--white);text-align:center;padding-top:24px}
.tile .ico{width:76px;height:76px;border-radius:50%;background:var(--white);margin:0 auto 10px;display:flex;align-items:center;justify-content:center}
.tile h3{font-family:"Exo 2",sans-serif;font-weight:600;font-size:19px;margin-bottom:8px}
.tile p{font-size:11px;line-height:20px;color:rgba(255,255,255,.8);padding:0 42px}
.t-teal{background:var(--teal)}.t-blue{background:var(--blue)}.t-green{background:var(--green)}

/* people */
.people-arc{left:0;top:1232px;width:300px;height:80px}
.people-blob{left:304px;top:1438px;width:266px;height:272px;border-radius:50%;background:var(--teal)}
.people-photo{left:0;top:1298px;width:491px;height:337px;border-radius:0 18px 18px 0;background:linear-gradient(120deg,#3d3a44,#8b7a63 45%,#d9b46a 60%,#6b5c52)}
.people-title{left:681px;top:1308px;font-size:36px}
.people-sub{left:681px;top:1354px}
.people-copy{left:681px;top:1392px;width:350px}
.pill{left:681px;width:240px;height:36px;border-radius:18px;background:var(--pill);border:1.5px solid #9dbbe8;display:flex;align-items:center;padding-left:6px;gap:12px;font-size:13px;font-weight:500;color:var(--ink)}
.pill .tick{width:26px;height:26px;border-radius:50%;border:2px solid var(--blue);display:flex;align-items:center;justify-content:center}

/* projects */
.projects-title{top:1772px;left:0;width:1200px;font-size:36px}
.projects-sub{top:1820px;left:0;width:1200px}
.card{top:1876px;width:245px;height:304px;border:1px solid var(--line);background:var(--white)}
.card .img{height:217px}
.card h4{font-size:13.5px;font-weight:600;margin:22px 0 4px 15px}
.card p{font-size:11.5px;color:var(--muted);margin-left:17px}

/* subscribe */
.banner{left:0;top:2255px;width:1200px;height:345px;background:linear-gradient(180deg,#4a5a60 0%,#2f3a38 40%,#3a3526 75%,#232019 100%)}
.banner-title{top:2347px;left:0;width:1200px;font-family:"Exo 2",sans-serif;font-weight:500;font-size:36px;line-height:42px;color:var(--white)}
.subscribe{left:336px;top:2461px;width:529px;height:38px;display:flex;border-radius:19px;overflow:hidden}
.subscribe .field{flex:1;background:var(--white);font-size:11px;color:var(--muted);padding:12px 0 0 20px}
.subscribe .btn{width:122px;background:var(--teal);color:var(--white);font-size:14px;font-weight:500;text-align:center;padding-top:9px}

/* faq */
.faq-title{left:129px;top:2686px;font-size:36px;line-height:45px}
.faq-q{left:169px;font-size:14.5px;font-weight:500;line-height:22px;width:350px}
.faq-a{left:169px;top:2856px;width:330px;font-size:11.5px}
.faq-sign{left:131px;width:18px;height:18px}
.faq-rule{left:129px;width:370px;height:1px;background:var(--line)}
.faq-blob-top{left:680px;top:2709px;width:510px;height:300px;border-radius:50%;background:var(--teal)}
.faq-blob-bot{left:830px;top:2930px;width:300px;height:226px;border-radius:50%;background:var(--blue)}
.faq-photo{left:708px;top:2752px;width:492px;height:337px;border-radius:22px 0 0 22px;background:radial-gradient(circle at 55% 45%,#f3e3c0 0%,#c9a36a 30%,#6a6a47 65%,#3b4330 100%)}

/* resources */
.res-title{top:3238px;left:0;width:1200px;font-size:36px}
.res{top:3313px;width:309px}
.res .img{height:227px}
.res h4{margin-top:30px;padding-left:22px;border-left:4px solid var(--teal);font-family:"Exo 2",sans-serif;font-weight:500;font-size:19px;line-height:20px}
.res p{font-size:11.5px;color:var(--muted);line-height:19px;margin:8px 0 0 24px;width:280px}
.res a{display:block;margin:6px 0 0 26px;font-size:12px;color:var(--blue)}

/* footer */
.footer-bg{left:0;top:3700px;width:1200px;height:415px}
.footer-mark{left:566px;top:3713px;width:68px;height:68px;border-radius:50%;background:var(--white);border:3px solid #d7e5f5}
.foot-brand{left:118px;top:3868px;width:140px;text-align:center;color:var(--white);font-family:"Exo 2",sans-serif;font-weight:600;font-size:16px;line-height:20px}
.foot-brand i{display:block;width:44px;height:44px;border-radius:50%;border:2px solid var(--white);margin:0 auto 10px}
.social{left:126px;top:3976px;display:flex;gap:8px}
.social i{width:34px;height:34px;border-radius:50%;border:1.5px solid rgba(255,255,255,.6)}
.foot-h{top:3844px;color:var(--white);font-size:14px;font-weight:500}
.foot-txt{color:var(--white);font-size:12px;line-height:20px}
.foot-row{left:336px;display:flex;gap:16px;align-items:flex-start}
.sitemap{left:612px;top:3876px;list-style:none}
.sitemap li{color:var(--white);font-size:11.5px;line-height:24px;padding-left:18px;position:relative}
.sitemap li::before{content:"";position:absolute;left:0;top:10px;width:5px;height:5px;border-radius:50%;background:var(--teal)}
.news-copy{left:887px;top:3876px;width:250px;font-size:11.5px}
.news-field{left:887px;top:3931px;width:250px;height:38px;border-radius:19px;background:var(--white);font-size:11px;color:var(--muted);padding:12px 0 0 18px}
.news-field b{position:absolute;right:4px;top:4px;width:30px;height:30px;border-radius:50%;background:var(--teal);display:flex;align-items:center;justify-content:center}
.copyright{top:4084px;left:0;width:1200px;text-align:center;font-size:11px;color:var(--white)}
</style>
</head>
<body>

<!-- header & hero background -->
<svg class="abs hero-shape" viewBox="0 0 1200 720" aria-hidden="true">
  <defs>
    <linearGradient id="heroGrad" x1="0" y1="0" x2="1" y2="1">
      <stop offset="0" stop-color="#ffffff"/>
      <stop offset=".22" stop-color="#2cc3a6"/>
      <stop offset=".7" stop-color="#12b293"/>
      <stop offset="1" stop-color="#0a9a72"/>
    </linearGradient>
    <linearGradient id="blueBlob" x1="0" y1="0" x2="1" y2="1">
      <stop offset="0" stop-color="#1b73d3"/>
      <stop offset="1" stop-color="#0a3f95"/>
    </linearGradient>
  </defs>
  <path d="M0 0 H607 C612 330 470 640 90 708 Q40 716 0 705 Z" fill="url(#heroGrad)"/>
  <path d="M1200 555 C1150 550 1120 585 1115 620 C1060 640 1040 660 1018 668 C1050 705 1110 722 1160 712 C1185 706 1200 695 1200 690 Z" fill="url(#blueBlob)"/>
</svg>

<div class="abs brand">
  <div class="brand-dot"></div>
  <div class="brand-name">Wellness, Meaning, and the Inner Journey<span>The Research Program</span></div>
</div>

<nav class="abs nav">
  <a class="active" href="#" style="left:0">Home</a>
  <a href="#" style="left:56px">People</a>
  <a href="#" style="left:115px">Projects</a>
  <a href="#" style="left:184px">FAQs</a>
  <a href="#" style="left:233px">Resources</a>
  <a href="#" style="left:313px">Contact</a>
</nav>

<div class="abs call">
  <svg width="20" height="20" viewBox="0 0 24 24"><path d="M6.6 10.8a15 15 0 0 0 6.6 6.6l2.2-2.2c.3-.3.7-.4 1-.2 1.1.4 2.3.6 3.6.6.6 0 1 .4 1 1V20c0 .6-.4 1-1 1A17 17 0 0 1 3 4c0-.6.4-1 1-1h3.5c.6 0 1 .4 1 1 0 1.3.2 2.5.6 3.6.1.3 0 .7-.2 1z" fill="#34d8a8"/></svg>
  <small>Call Us On :</small>
  <b>555 014 2290</b>
</div>

<h1 class="abs hero-title">Research<br>Program<br><em>For the Bright<br>Future !</em></h1>
<p class="abs hero-lede">We serve a new RESEARCH PROGRA at the Harrowgate University School of Medicine</p>

<div class="abs hero-icons">
  <div class="hero-icon">
    <svg width="50" height="46" viewBox="0 0 50 46" fill="none" stroke="#fff" stroke-width="2"><path d="M25 42 6 23a11 11 0 0 1 19-15 11 11 0 0 1 19 15z"/><path d="M14 26l8-8 6 5 8-7"/></svg>
    Healthcare
  </div>
  <div class="hero-icon">
    <svg width="56" height="46" viewBox="0 0 56 46" fill="none" stroke="#fff" stroke-width="2"><path d="M14 4h28l12 12-26 28L2 16z"/><path d="M2 16h52M20 4l-6 12 14 28 14-28-6-12"/></svg>
    Values
  </div>
  <div class="hero-icon">
    <svg width="46" height="46" viewBox="0 0 46 46" fill="none" stroke="#fff" stroke-width="2"><circle cx="23" cy="18" r="8"/><path d="M23 2v5M23 29v15M9 18H4M42 18h-5M12 7l3 3M34 7l-3 3M16 44V32h14v12"/></svg>
    Spiritual Life
  </div>
</div>

<div class="abs dots"><i></i><i class="on"></i><i></i><i></i><i></i></div>

<div class="abs hero-photo" role="img" aria-label="Bright atrium with tall columns, indoor plants and people seated at tables"></div>

<!-- vision -->
<h2 class="abs heading center vision-title">Our Vision</h2>
<div class="abs center vision-sub tagline"><span style="font-size:15px">Wellness, Meaning and the Inner Journey</span><span>The Research Program</span></div>
<p class="abs copy center vision-copy">Lorem Ipsum has been the industry's standard dummy text ever since the 1500s, when an unknown printer took a galley of type and scrambled it to make a type specimen book. It has survived not only five centuries.</p>

<div class="abs tiles">
  <div class="tile t-teal">
    <div class="ico"><svg width="40" height="40" viewBox="0 0 40 40" fill="none" stroke="#12b69c" stroke-width="2"><circle cx="20" cy="13" r="7"/><path d="M6 36c2-9 8-13 14-13s12 4 14 13"/></svg></div>
    <h3>People</h3><p>Lorem Ipsum has been the industry's standard</p>
  </div>
  <div class="tile t-blue">
    <div class="ico"><svg width="40" height="40" viewBox="0 0 40 40" fill="none" stroke="#0b4fae" stroke-width="2"><circle cx="17" cy="23" r="7"/><circle cx="17" cy="23" r="2.5"/><path d="M17 12v4M17 30v4M6 23h4M24 23h4M25 15c4-8 9-10 11-10 0 2-2 7-10 11"/></svg></div>
    <h3>Research Projects</h3><p>Lorem Ipsum has been the industry's standard</p>
  </div>
  <div class="tile t-green">
    <div class="ico"><svg width="40" height="40" viewBox="0 0 40 40" fill="none" stroke="#4f9f3a" stroke-width="2"><circle cx="16" cy="18" r="6"/><path d="M5 36c1-7 6-10 11-10s10 3 11 10"/><circle cx="30" cy="10" r="6"/><path d="M28.5 8.5a1.8 1.8 0 1 1 2 2v1.5M30 14v.3"/></svg></div>
    <h3>Faq's</h3><p>Lorem Ipsum has been the industry's standard</p>
  </div>
</div>

<!-- people -->
<svg class="abs people-arc" viewBox="0 0 300 80" aria-hidden="true"><path d="M0 80 Q40 20 150 10 Q240 5 300 70 V80 Z" fill="#0b4fae"/></svg>
<div class="abs people-blob"></div>
<div class="abs people-photo" role="img" aria-label="Group of colleagues holding glowing light bulbs together"></div>

<h2 class="abs heading people-title">People</h2>
<p class="abs tagline people-sub">Wellness, Meaning and the Inner Journey</p>
<p class="abs copy people-copy">Lorem Ipsum has been the industry's standard dummy text ever since the 1500s, when an unknown printer took a galley of type and scrambled it to make a type specimen book. It has survived not only five centuries.</p>

<div class="abs pill" style="top:1493px"><span class="tick"><svg width="14" height="14" viewBox="0 0 14 14"><path d="M2 7l3.5 3.5L12 3" fill="none" stroke="#0b4fae" stroke-width="2"/></svg></span>Research Team</div>
<div class="abs pill" style="top:1538px"><span class="tick"><svg width="14" height="14" viewBox="0 0 14 14"><path d="M2 7l3.5 3.5L12 3" fill="none" stroke="#0b4fae" stroke-width="2"/></svg></span>Advisory Committee</div>
<div class="abs pill" style="top:1583px"><span class="tick"><svg width="14" height="14" viewBox="0 0 14 14"><path d="M2 7l3.5 3.5L12 3" fill="none" stroke="#0b4fae" stroke-width="2"/></svg></span>Partners</div>

<!-- projects -->
<h2 class="abs heading center projects-title">Projects</h2>
<p class="abs center tagline projects-sub">Wellness, Meaning and the Inner Journey</p>

<div class="abs card" style="left:89px"><div class="img" role="img" aria-label="Audience in a lecture hall facing a presentation screen" style="background:linear-gradient(180deg,#9aa9bd,#3a4a6a 60%,#1c2a55)"></div><h4>Your Personal Spiritual Coach</h4><p>Lorem Ipsum has been the.</p></div>
<div class="abs card" style="left:348px"><div class="img" role="img" aria-label="Woman meditating cross-legged among red desert rocks" style="background:linear-gradient(180deg,#7fa6c9,#b4663d 45%,#8b4a2e 75%,#5e6b4a)"></div><h4>Beyond Religion</h4><p>Lorem Ipsum has been the.</p></div>
<div class="abs card" style="left:607px"><div class="img" role="img" aria-label="Silhouetted cross and couple against a sunset sea" style="background:linear-gradient(180deg,#e8a23a,#c8631d 45%,#3a2214 80%,#1a110b)"></div><h4>Turn Your Life Up</h4><p>Lorem Ipsum has been the.</p></div>
<div class="abs card" style="left:865px"><div class="img" role="img" aria-label="Person sitting by a calm mountain lake framed by trees" style="background:linear-gradient(180deg,#5b7b3e,#b9c8c7 40%,#8aa1a3 65%,#3d5030)"></div><h4>Your Personal Spiritual Coach</h4><p>Lorem Ipsum has been the.</p></div>

<!-- subscribe -->
<div class="abs banner" role="img" aria-label="Misty canyon landscape at dusk with figures on a cliff edge"></div>
<h2 class="abs center banner-title">Learn More About Spiritual<br>Traditions !</h2>
<div class="abs subscribe"><div class="field">Enter Email *</div><div class="btn">SUBSCRIBE</div></div>

<!-- faq -->
<h2 class="abs heading faq-title">Frequently Asked<br>Questions</h2>

<svg class="abs faq-sign" style="top:2827px" viewBox="0 0 18 18"><path d="M9 1v16M1 9h16" stroke="#12b69c" stroke-width="2"/></svg>
<p class="abs faq-q" style="top:2824px">What makes this project unique?</p>
<p class="abs copy faq-a">Lorem Ipsum has been the industry's standard dummy text ever since the when an unknown printer took a galley of type and scrambled has been.</p>
<div class="abs faq-rule" style="top:2940px"></div>

<svg class="abs faq-sign" style="top:2966px" viewBox="0 0 18 18"><path d="M1 9h16" stroke="#12b69c" stroke-width="2"/></svg>
<p class="abs faq-q" style="top:2953px">Does this Project Assume that the Impact of Religion Is Always Positive?</p>
<div class="abs faq-rule" style="top:3020px"></div>

<svg class="abs faq-sign" style="top:3038px" viewBox="0 0 18 18"><path d="M1 9h16" stroke="#12b69c" stroke-width="2"/></svg>
<p class="abs faq-q" style="top:3036px">How Can I Collaborate?</p>
<div class="abs faq-rule" style="top:3076px"></div>

<svg class="abs faq-sign" style="top:3091px" viewBox="0 0 18 18"><path d="M1 9h16" stroke="#12b69c" stroke-width="2"/></svg>
<p class="abs faq-q" style="top:3089px">Will Harrowgate U Faculty Lead All Projects?</p>

<div class="abs faq-blob-top"></div>
<div class="abs faq-blob-bot"></div>
<div class="abs faq-photo" role="img" aria-label="Open hands holding a glowing brain shape against a warm field at sunset"></div>

<!-- resources -->
<h2 class="abs heading center res-title">Resources</h2>
<div class="abs res" style="left:276px">
  <div class="img" role="img" aria-label="Many hands gathered around a wooden cross" style="background:linear-gradient(135deg,#4a3a2e,#a27a55 50%,#5a4636)"></div>
  <h4>Diverse Religious</h4>
  <p>Lorem Ipsum has been the industry's standard dummy text ever since th</p>
  <a href="#">Read More</a>
</div>
<div class="abs res" style="left:615px">
  <div class="img" role="img" aria-label="Person in traditional ceremonial dress with colourful headwear" style="background:linear-gradient(135deg,#2d3b2a,#6a5a3a 40%,#b8332c 65%,#2a2a3a)"></div>
  <h4>Spiritual Traditions</h4>
  <p>Lorem Ipsum has been the industry's standard dummy text ever since th</p>
  <a href="#">Read More</a>
</div>

<!-- footer -->
<svg class="abs footer-bg" viewBox="0 0 1200 415" aria-hidden="true">
  <defs>
    <linearGradient id="footGrad" x1="0" y1="1" x2="1" y2="0">
      <stop offset="0" stop-color="#0a3f95"/>
      <stop offset=".5" stop-color="#0b66b8"/>
      <stop offset="1" stop-color="#12b69c"/>
    </linearGradient>
  </defs>
  <path d="M0 135 Q600 -20 1200 135 V415 H0 Z" fill="url(#footGrad)"/>
  <path d="M0 140 Q600 -15 1200 140" fill="none" stroke="#0b4fae" stroke-width="2"/>
</svg>
<div class="abs footer-mark"></div>

<div class="abs foot-brand"><i></i>Wellness, Meaning &amp; the Inner Journey</div>
<div class="abs social"><i></i><i></i><i></i></div>

<p class="abs foot-h" style="left:336px">Contact Us</p>
<div class="abs foot-row" style="top:3876px">
  <svg width="16" height="22" viewBox="0 0 16 22"><path d="M8 1a7 7 0 0 0-7 7c0 5 7 13 7 13s7-8 7-13a7 7 0 0 0-7-7z" fill="#12b69c"/><circle cx="8" cy="8" r="2.5" fill="#0b4fae"/></svg>
  <p class="foot-txt">WMIJ<br>101 - lorem ipsum simple text<br>print type industry text!</p>
</div>
<div class="abs foot-row" style="top:3955px">
  <svg width="16" height="16" viewBox="0 0 24 24"><path d="M6.6 10.8a15 15 0 0 0 6.6 6.6l2.2-2.2c.3-.3.7-.4 1-.2 1.1.4 2.3.6 3.6.6.6 0 1 .4 1 1V20c0 .6-.4 1-1 1A17 17 0 0 1 3 4c0-.6.4-1 1-1h3.5c.6 0 1 .4 1 1 0 1.3.2 2.5.6 3.6.1.3 0 .7-.2 1z" fill="#12b69c"/></svg>
  <p class="foot-txt" style="font-size:13px">555 014 2290</p>
</div>
<div class="abs foot-row" style="top:3990px">
  <svg width="16" height="14" viewBox="0 0 16 14"><rect x="0" y="1" width="16" height="12" rx="1.5" fill="#12b69c"/><path d="M1 2l7 6 7-6" fill="none" stroke="#0b4fae" stroke-width="1.5"/></svg>
  <p class="foot-txt">info@wmij-research.org</p>
</div>

<p class="abs foot-h" style="left:612px">Sitemap</p>
<ul class="abs sitemap">
  <li>Home</li><li>People</li><li>Projects</li><li>Faq's</li><li>Resources</li><li>Contact</li>
</ul>

<p class="abs foot-h" style="left:887px">Newsletter Signup !</p>
<p class="abs foot-txt news-copy">Would you like to receive our exclusive update for signup Today !</p>
<div class="abs news-field">Enter Email *<b><svg width="14" height="14" viewBox="0 0 14 14"><path d="M1 6.5 13 1 8.5 13 6.5 7.5z" fill="#fff"/></svg></b></div>

<p class="abs copyright">©WMIJ Research Program - 2021 All rights reserved</p>

</body>
</html>
```